Dental office stationary (letterhead, envelopes), business cards, presentation folders

Nothing too dental outside of the logo. I will need all stationary, presentation folders, business cards. Would prefer to stay in the colors of the logo

Gordon Patel, DDS
Bright Haven Dental Implant Center
555-318-2790
info@brighthavendental.example
4817 NW Maple Crest Rd Unit B
Stuart, FL 00000

Also need appointment date and time
And cancellation policy
I want it to say “kindly ask for
A 48hr cancellation policy to avoid incurring a cancellation fee”

Industry/Entity Type

Dental

Colors
0054AA
0677BA
7BADD7
CADEEF
E8F1F8

Requirements
Must have
• Name of your office, name of doctor, address, phone number
Should not have
• Too much tooth/dental. Only the tooth in logo

```html
<!DOCTYPE html>
<html lang="en">
<head>
<meta charset="utf-8">
<title>Bright Haven Dental Implant Center – Stationery</title>
<link href="https://fonts.googleapis.com/css2?family=Roboto:wght@400;500;700&family=Arimo:wght@400&display=swap" rel="stylesheet">
<style>
  :root{
    --backdrop:#9a9899;
    --paper:#ffffff;
    --band-light:#cfe9f6;
    --band-mid:#7fc3e6;
    --deep-blue:#0a67b6;
    --emboss-blue:#0a4c94;
    --teal:#15b89a;
    --logo:#14a9d6;
    --rule:#0b62b8;
    --ink:#555555;
    --ink-dark:#3d3d3d;
  }
  *{box-sizing:border-box;margin:0;padding:0}
  html,body{width:1200px;height:893px;overflow:hidden}
  body{background:var(--backdrop);font-family:"Roboto",sans-serif;color:var(--ink);position:relative}
  .sheet{position:absolute;background:var(--paper);overflow:hidden}
  .footer-band{position:absolute;left:0;bottom:0;width:100%;background:linear-gradient(180deg,var(--band-light),var(--band-mid))}
  .brand-name{font-family:"Roboto",sans-serif;font-weight:400;color:var(--logo);white-space:nowrap;letter-spacing:.5px;position:absolute}
  address{font-style:normal}

  /* Letterhead */
  .letterhead{left:72px;top:105px;width:483px;height:683px}
  .letterhead .brand-name{left:34px;top:46px;font-size:27px}
  .letterhead .footer-band{height:58px}
  .letterhead .contact{position:absolute;left:335px;top:30px;border-left:1px solid var(--teal);padding-left:7px;font-size:8.2px;line-height:10.2px;color:var(--ink-dark)}
  .contact .gap{height:5px}
  .icon{display:inline-block;border-radius:50%;background:var(--teal)}
  .contact .icon{width:6px;height:6px;margin-right:3px}
  .web em{font-style:normal;color:var(--teal)}
  .letter{position:absolute;left:43px;top:210px;width:398px;font-family:"Arimo",sans-serif;font-size:8px;line-height:10px;color:var(--ink)}
  .letter .salutation{font-family:"Roboto",sans-serif;font-size:10.5px;font-weight:500;color:var(--ink-dark);margin-bottom:20px}
  .letter p{margin-bottom:8.5px}
  .letter .closing{font-family:"Roboto",sans-serif;font-size:6px;font-weight:700;color:var(--ink-dark);margin-top:15px}
  .signature{position:absolute;left:45px;top:477px;width:60px;height:20px;background:linear-gradient(90deg,#e6e6e6,#d4d4d4);border-radius:2px}

  /* Business cards */
  .card-front{left:592px;top:105px;width:259px;height:148px}
  .card-front .brand-name{left:14px;top:69px;font-size:13px}
  .card-front .footer-band{height:28px}
  .card-front .details{position:absolute;left:130px;top:39px;height:69px;border-left:1px solid var(--rule);padding-left:7px;font-size:6.2px;line-height:8.2px;color:var(--ink-dark)}
  .details .doctor{font-size:8px;font-weight:700;color:var(--logo);line-height:9px}
  .details .gap{height:4px}
  .details .icon{width:4.5px;height:4.5px;margin-right:2px}
  .card-back{left:869px;top:105px;width:259px;height:148px;background:var(--deep-blue)}
  .card-back .brand-name{left:0;width:100%;text-align:center;top:62px;font-size:22px;color:var(--emboss-blue)}

  /* Envelopes */
  .envelope-back{left:592px;top:287px;width:536px;height:232px}
  .envelope-back .flap{position:absolute;left:0;top:0;width:536px;height:66px}
  .envelope-back .brand-name{left:0;width:100%;text-align:center;top:24px;font-size:19px}
  .envelope-front{left:592px;top:556px;width:536px;height:232px}
  .envelope-front .footer-band{height:60px}
  .envelope-front .brand-name{left:10px;top:32px;font-size:18px;width:150px;text-align:center}
  .envelope-front .return-address{position:absolute;left:10px;top:64px;width:150px;text-align:center;font-size:7.6px;line-height:10px;color:var(--ink-dark)}
</style>
</head>
<body>

<!-- Letterhead -->
<section class="sheet letterhead">
  <div class="brand-name">BRIGHT HAVEN</div>
  <address class="contact">
    4817 NW Maple Crest Rd Unit B<br>Lakemont, OR 00000
    <div class="gap"></div>
    <span class="icon"></span>555-318-2790<br>
    <span class="icon"></span>info@brighthavendental.example<br>
    <span class="web"><span class="icon"></span>www.<em>brighthavendental</em>.example</span>
  </address>
  <div class="letter">
    <div class="salutation">Dear Mr. Alder,</div>
    <p>Lorem ipsum dolor sit amet, consectetuer adipiscing elit, sed diam nonmmy nibh euismod tincidunt ut laor eet dolore magna aliquam erat volutpat. Ut wisi enim ad minim veniam, quis nostrud exerci tationmcorper suscipit lobortis nisl ut aliquip ex ea commodo consequat. Duis autem vel eum iriure dolor in hendrerit in vulputate velit esse molestie consequat, vel illum dolore eu feugiat</p>
    <p>Rorem ipsum dolor sit amet, consectetuer adipiscing elit, sed diam nonmmy nibh euismod tincidunt ut laor eet dolore magna aliquam erat volutpat. Ut wisi enim ad minim veniam, quis nostrud exerci tationmcorper suscipit lobortis nisl ut aliquip ex ea commodo consequat. Duis autem vel eum iriure dolor in hendrerit in vulputate velit esse molest</p>
    <p>Dorem ipsum dolor sit amet, consectetuer adipiscing elit, sed diam nonmmy nibh euismod tincidunt ut laor eet dolore magna aliquam erat volutpat. Ut wisi enim ad minim veniam, quis nostrud exerci tationmcorper suscipit lobortis nisl ut aliquip ex ea commodo consequat. Duis autem vel eum iriure dolor in hendrerit in suscipit lobortis nisl ut aliquip ex ea commodo consequat. Duis autem vel eum iriure dolor in hendrerit in vulputate velit esse molestie consequat, vel illum</p>
    <p>Sorem ipsum dolor sit amet, consectetuer adipiscing elit, sed diam nonmmy nibh euismod tincidunt ut laor eet dolore magna aliquam erat volutpat. Ut wisi enim ad minim veniam, quis nostrud exerci tationmcorper suscipit lobortis nisl ut aliquip ex ea commodo consequat. Duis autem vel eum iriure dolor in</p>
    <div class="closing">Sincerely,</div>
  </div>
  <div class="signature" role="img" aria-label="Handwritten signature"></div>
  <div class="footer-band" role="img" aria-label="Decorative footer band in blue and teal brand tones"></div>
</section>

<!-- Business card, front -->
<section class="sheet card-front">
  <div class="brand-name">BRIGHT HAVEN</div>
  <div class="details">
    <div class="doctor">Gordon Patel, DDS</div>
    Bright Haven Dental Implant Center
    <div class="gap"></div>
    4817 NW Maple Crest Rd Unit B<br>Lakemont, OR 00000
    <div class="gap"></div>
    <span class="icon"></span>555-318-2790<br>
    <span class="icon"></span>info@brighthavendental.example<br>
    <span class="web"><span class="icon"></span>www.<em>brighthavendental</em>.example</span>
  </div>
  <div class="footer-band" role="img" aria-label="Decorative footer band in blue and teal brand tones"></div>
</section>

<!-- Business card, back -->
<section class="sheet card-back">
  <div class="brand-name">BRIGHT HAVEN</div>
</section>

<!-- Envelope, back with flap -->
<section class="sheet envelope-back">
  <svg class="flap" viewBox="0 0 536 66" preserveAspectRatio="none">
    <path d="M3,4 Q8,38 18,55 Q24,64 40,64 L496,64 Q512,64 520,52 Q530,36 534,4" fill="none" stroke="#d8d8d8" stroke-width="1.2"/>
  </svg>
  <div class="brand-name">BRIGHT HAVEN</div>
</section>

<!-- Envelope, front -->
<section class="sheet envelope-front">
  <div class="brand-name">BRIGHT HAVEN</div>
  <address class="return-address">4817 NW Maple Crest Rd Unit B<br>Lakemont, OR 00000</address>
  <div class="footer-band" role="img" aria-label="Decorative footer band in blue and teal brand tones"></div>
</section>

</body>
</html>
```